Fun, Clean Business Card For Family Focused Travel Agency

I need a business card using specific colors and fonts as in the uploaded files. Ideally, I would like a large image of the logo on the back and all the contact info on the front. Maybe the stars/dots somewhere in a flowy form.

I do want it the contact information to be clear and easy to read. I don't want it to look too busy. Maybe even a bit minimalist.

I plan or ordering the ROUNDED CORNER business cards from Cardwell Press, so please consider that in your design.

Target Market(s)

Families with children, couples, groups of friends

Contact Information for Business Card

Marla Quint, Owner
Marla@TumbleTrips.example
Cell Phone Number 555-218-4603
Office Phone Number 555-647-1925
Specializing in Glimmerland destinations, Pelican Bay Fun Park, Cruises and All-Inclusive Vacations.

Nice but not required:
www.TumbleTrips.example
Facebook, Instagram, Twitter icons with username: TumbleTrips

Font styles to use
Sans Serif

Requirements
Must have
• Please try to use the colors from the logo as much as possible. I understand lighter shades/colors may be needed for some things.
Should not have
• NO SERIF FONTS. That is really the only thing I do not want at all

```html
<!DOCTYPE html>
<html lang="en">
<head>
<meta charset="utf-8">
<title>Tumble Trips – Business Card</title>
<link rel="stylesheet" href="https://fonts.googleapis.com/css2?family=Fira+Sans:wght@400;600;700&display=swap">
<style>
  :root {
    --backdrop: #6b6b6b;
    --card-white: #ffffff;
    --navy: #0d1530;
    --teal: #1aae94;
    --orange: #ef7d22;
    --yellow: #f1b420;
    --sky: #1fa3d9;
    --lime: #9cc73a;
    --text-dark: #1a1a1a;
    --divider: #d4d4d4;
  }
  * { box-sizing: border-box; margin: 0; padding: 0; }
  html, body { width: 1200px; height: 802px; overflow: hidden; }
  body {
    background: var(--backdrop);
    font-family: "Fira Sans", sans-serif;
    position: relative;
  }
  .card {
    position: absolute;
    top: 274px;
    width: 443px;
    height: 265px;
    box-shadow: 0 3px 8px rgba(0,0,0,.35);
  }
  .card-front { left: 136px; background: var(--card-white); }
  .card-back {
    left: 624px;
    background: linear-gradient(33deg,
      var(--navy) 0%, var(--navy) 12%, var(--teal) 30%,
      var(--orange) 48%, var(--yellow) 62%, var(--sky) 76%, var(--lime) 92%);
    color: #fff;
  }
  .front-brand {
    position: absolute;
    left: 20px; top: 118px;
    width: 170px;
    display: flex; align-items: center; justify-content: center; gap: 6px;
    color: var(--navy);
    font-weight: 700;
    font-size: 18px;
  }
  .brand-dot {
    width: 12px; height: 12px; border-radius: 50%;
    background: var(--orange);
  }
  .front-divider {
    position: absolute;
    left: 192px; top: 62px;
    width: 1px; height: 142px;
    background: var(--divider);
  }
  .contact-block { position: absolute; left: 213px; top: 72px; }
  .person-name {
    font-weight: 700; font-size: 20px; color: var(--navy);
    letter-spacing: .2px; line-height: 1.1;
  }
  .person-role { font-size: 13px; color: var(--teal); margin-top: 2px; }
  .contact-list { list-style: none; margin-top: 10px; }
  .contact-list li {
    display: flex; align-items: center; gap: 5px;
    font-size: 13px; color: var(--text-dark); line-height: 18px;
  }
  .contact-list svg { width: 11px; height: 11px; fill: var(--text-dark); flex: none; }
  .back-brand {
    position: absolute;
    left: 0; right: 0; top: 96px;
    text-align: center;
    font-weight: 700;
    font-size: 40px;
    line-height: 1;
  }
  .back-rule {
    position: absolute;
    left: 36px; right: 36px; top: 200px;
    height: 1px; background: rgba(255,255,255,.35);
  }
  .tagline {
    position: absolute;
    left: 0; right: 0; top: 206px;
    text-align: center;
    font-size: 13.5px; line-height: 18px;
  }
</style>
</head>
<body>
  <section class="card card-front">
    <div class="front-brand"><span class="brand-dot"></span>Tumble Trips</div>
    <div class="front-divider"></div>
    <div class="contact-block">
      <div class="person-name">MARLA QUINT</div>
      <div class="person-role">Owner</div>
      <ul class="contact-list">
        <li><svg viewBox="0 0 16 16"><path d="M1 5c0-2 3-3 7-3s7 1 7 3v1h-4V5H5v1H1zM4 7h8l2 7H2z"/></svg>555-218-4603</li>
        <li><svg viewBox="0 0 16 16"><path d="M4 0h8a1 1 0 0 1 1 1v14a1 1 0 0 1-1 1H4a1 1 0 0 1-1-1V1a1 1 0 0 1 1-1zm1 2v10h6V2z"/></svg>555-647-1925</li>
        <li><svg viewBox="0 0 16 16"><path d="M0 3h16v10H0zm1.5 1.2V12h13V4.2L8 9z"/></svg>Marla@TumbleTrips.example</li>
        <li><svg viewBox="0 0 16 16"><circle cx="8" cy="8" r="7.5"/><path d="M4 5l3 1-1 3 3 2-1 3M11 3l-1 3 3 1" stroke="#fff" stroke-width="1.2" fill="none"/></svg>www.TumbleTrips.example</li>
      </ul>
    </div>
  </section>

  <section class="card card-back">
    <div class="back-brand">Tumble Trips</div>
    <div class="back-rule"></div>
    <p class="tagline">Specializing in Glimmerland destinations, Pelican Bay Fun Park<br>Cruises and All-Inclusive Vacations</p>
  </section>
</body>
</html>
```